VORNAK SYSTEMS BUSINESS CARD DESIGN

WE WANT COMPLETE NEW DESIGN OF OUR BUSINESS CARD. WE ARE AN INTEGRATION COMPANY, WHERE WE INTEGRATE IOT/SMART SYSTEMS TO HOMES AND CORPORATE CUSTOMERS. WE SUPPLY AND INSTALL AUTOMATION PRODUCTS. THE FINAL DESIGN SHOULD COMMUNICATE TECHNOLOGY. THE CARD DESIGN SHOULD BE VERY IMPACT FULL. LOGO NEEDS TO BE THERE. IT WOULD NICE IF THE DESIGN WAS CLEAN. COLORS IS UP TO DESIGNER TO PLAY WITH, OR CAN STICK TO CORPORATE COLORS (FOLLOW LOGO). I HAVE ADDED FEW REFERENCE PHOTOS TO DRAW INSPIRATION MAYBE. I HAVE ADDED A HEX DESIGN, ITS NOT NECESSARY TO USE THIS DESIGN, ITS UPTO DESIGNER, JUST ADDED IF NEEDED TO PLAY WITH DESIGN.

Target Market(s)

Private end users and corporate clients

Industry/Entity Type

technology, home automation, home theaters, building management systems, IOT

Contact Information for Business Card

It should include Employee name, personal number, office number, email address, both in English and arabic. DETAILS TO INCLUDE :RAJESH PALLIVAL, MOBILE 0097150738265,OFFCIE 009714368547, RAJESH@VORNAKSYS.EXAMPLE

Requirements
Must have
• Should feel like a technology company from design. Details both and in English and arabic (or at least have provision for arabic in design).
Nice to have
• I would like logo on one side, and details on the other side. Logo design side should communicate technology with logo. Other side can be clean just with information or also have some design aspects following from logo side. it would be interesting to see submissions with square design as well (that looks like an app Icon). colors could be of logo, red black grey and white. I have added some designs to draw inspiration from

```html
<!DOCTYPE html>
<html lang="en">
<head>
<meta charset="utf-8">
<title>Vornak Systems – Business Card</title>
<link rel="stylesheet" href="https://fonts.googleapis.com/css2?family=Arimo:wght@400;700&family=Noto+Kufi+Arabic:wght@400;700&display=swap">
<style>
  :root {
    --backdrop: #1d1d1e;
    --card: #f4f4f2;
    --ink: #141414;
    --brand-red: #e3202a;
    --muted: #7d7d7d;
    --rule: #9a9a9a;
  }
  * { margin: 0; padding: 0; box-sizing: border-box; }
  html, body {
    width: 1200px; height: 963px; overflow: hidden;
    background: var(--backdrop);
    font-family: "Arimo", Arial, sans-serif;
  }
  .canvas {
    position: relative; width: 1200px; height: 963px;
    display: flex; align-items: center; justify-content: center;
  }
  .card {
    position: relative; width: 880px; height: 503px;
    background: var(--card);
  }
  .identity {
    position: absolute; left: 56px; top: 150px;
  }
  .identity__name {
    color: var(--brand-red); font-weight: 700; font-size: 26px; letter-spacing: 0.2px; line-height: 30px;
  }
  .identity__role {
    color: var(--muted); font-size: 20px; line-height: 24px; margin-top: 4px;
  }
  .divider {
    position: absolute; left: 56px; right: 60px; top: 232px;
    height: 1px; background: var(--rule);
  }
  .contacts {
    position: absolute; left: 56px; top: 252px; list-style: none;
  }
  .contacts__item {
    display: flex; align-items: center; gap: 14px;
    color: var(--muted); font-size: 20px; line-height: 32px;
  }
  .contacts__icon { width: 16px; height: 16px; flex: none; }
  .brand {
    position: absolute; right: 60px; top: 104px;
  }
  .brand__lockup { display: flex; align-items: center; gap: 14px; }
  .brand__dot {
    width: 36px; height: 36px; border-radius: 50%;
    background: var(--brand-red); flex: none;
  }
  .brand__name {
    color: var(--ink); font-weight: 700; font-size: 38px; line-height: 46px; letter-spacing: 2px;
  }
  .brand__tagline {
    color: var(--ink); font-size: 15px; letter-spacing: 5px; margin-top: 14px; padding-left: 50px;
  }
  .arabic {
    position: absolute; right: 60px; top: 256px;
    direction: rtl; text-align: right;
    font-family: "Noto Kufi Arabic", sans-serif;
  }
  .arabic__name { color: var(--brand-red); font-weight: 700; font-size: 22px; line-height: 36px; }
  .arabic__role { color: var(--muted); font-size: 17px; line-height: 30px; }
</style>
</head>
<body>
<main class="canvas">
  <article class="card">
    <section class="identity">
      <h1 class="identity__name">RAJESH PALLIVAL</h1>
      <p class="identity__role">General Manager</p>
    </section>

    <section class="brand">
      <div class="brand__lockup">
        <span class="brand__dot"></span>
        <span class="brand__name">VORNAK SYSTEMS</span>
      </div>
      <p class="brand__tagline">A VORNAK GROUP DIVISION.</p>
    </section>

    <div class="divider"></div>

    <ul class="contacts">
      <li class="contacts__item">
        <svg class="contacts__icon" viewBox="0 0 16 16" aria-hidden="true">
          <rect x="4" y="1" width="8" height="14" rx="1.5" fill="none" stroke="#e3202a" stroke-width="1.6"/>
          <line x1="7" y1="12.5" x2="9" y2="12.5" stroke="#e3202a" stroke-width="1.4"/>
        </svg>
        0097150738265
      </li>
      <li class="contacts__item">
        <svg class="contacts__icon" viewBox="0 0 16 16" aria-hidden="true">
          <path d="M3 1.5l3 .5 1 3.5-2 1.5c1 2 2.5 3.5 4.5 4.5l1.5-2 3.5 1 .5 3c-7 1-13-5-12-12z" fill="#e3202a"/>
        </svg>
        009714368547
      </li>
      <li class="contacts__item">
        <svg class="contacts__icon" viewBox="0 0 16 16" aria-hidden="true">
          <rect x="1" y="3" width="14" height="10" fill="none" stroke="#e3202a" stroke-width="1.5"/>
          <path d="M1 3l7 6 7-6" fill="none" stroke="#e3202a" stroke-width="1.5"/>
        </svg>
        RAJESH@VORNAKSYS.EXAMPLE
      </li>
    </ul>

    <section class="arabic" lang="ar">
      <p class="arabic__name">راجيش باليفال</p>
      <p class="arabic__role">المدير العام</p>
    </section>
  </article>
</main>
</body>
</html>
```